Health and wellnes company needs business cards

We are a Health and wellness business just relocated to Spain. Here nobody knows our business so we would like to put some of our services on the card. Clean design with logo.

Contact Information for Business Card

Brightmeadow
Paula & Oskar Dunbeck
Calle del Almendro 57
Villamar de la Costa
Mobile: 0046 731 402687
info@brightmeadow.example

Font styles to use
Serif

Colors
85cae6
85acd3
b768aa

Requirements
Must have
• these Services somewhere on the card
• - Private or group yoga
• - Reconnective healing
• - Kitesurfing lessons
• - Massage
• LOgo somewhere
Nice to have
• Colours that go with the logo please

```html
<!DOCTYPE html>
<html lang="en">
<head>
<meta charset="utf-8">
<title>Brightmeadow business card</title>
<link rel="stylesheet" href="https://fonts.googleapis.com/css2?family=Marcellus&family=Philosopher:wght@400;700&display=swap">
<style>
  :root {
    --page-bg: #e6e2dd;
    --card-navy: #1b2742;
    --card-navy-light: #2b3a5a;
    --card-teal: #2f7d74;
    --accent-teal: #4aa89c;
    --ring-teal: #3b9486;
    --text-light: #d9dee7;
    --text-muted: #c3cad6;
    --glass-light: #e9eeee;
    --glass-mid: #b9c9c6;
    --wordmark: #16233a;
  }
  * { margin: 0; padding: 0; box-sizing: border-box; }
  html, body {
    width: 1200px;
    height: 969px;
    overflow: hidden;
    background: var(--page-bg);
  }
  .card {
    position: absolute;
    left: 100px;
    top: 200px;
    width: 1000px;
    height: 570px;
    border-radius: 24px;
    overflow: hidden;
    background:
      radial-gradient(ellipse 420px 380px at 160px 250px, var(--card-navy-light), transparent 70%),
      linear-gradient(100deg, var(--card-navy) 0%, var(--card-navy) 48%, #1f4a5a 70%, var(--card-teal) 100%);
    box-shadow: 0 18px 40px rgba(20, 30, 50, 0.25);
  }
  .holders {
    position: absolute;
    left: 66px;
    top: 90px;
    font-family: "Philosopher", sans-serif;
    font-size: 26px;
    font-weight: 400;
    color: var(--accent-teal);
    letter-spacing: 0.3px;
    white-space: nowrap;
  }
  .services {
    position: absolute;
    left: 66px;
    top: 148px;
    list-style: none;
    font-family: "Marcellus", serif;
    font-size: 17px;
    line-height: 25px;
    color: var(--text-light);
    letter-spacing: 0.4px;
    white-space: nowrap;
  }
  .services li::before {
    content: "";
    display: inline-block;
    width: 6px;
    height: 6px;
    border-radius: 50%;
    background: var(--accent-teal);
    margin-right: 10px;
    vertical-align: 3px;
  }
  .address {
    position: absolute;
    left: 66px;
    top: 290px;
    font-family: "Philosopher", sans-serif;
    font-size: 20px;
    line-height: 27px;
    color: var(--text-muted);
    white-space: nowrap;
  }
  .contact {
    position: absolute;
    left: 66px;
    top: 400px;
    list-style: none;
    font-family: "Philosopher", sans-serif;
    font-size: 20px;
    line-height: 27px;
    color: var(--text-muted);
    white-space: nowrap;
  }
  .contact li { display: flex; align-items: center; }
  .contact svg { width: 16px; height: 16px; margin-right: 12px; flex: none; }
  .emblem {
    position: absolute;
    left: 409px;
    top: 9px;
    width: 552px;
    height: 552px;
    border-radius: 50%;
    border: 14px solid var(--ring-teal);
    box-shadow: 0 0 0 2px rgba(230, 240, 240, 0.55);
    background: radial-gradient(circle at 62% 30%, var(--glass-light) 0%, #d6dedd 40%, var(--glass-mid) 75%, #8fb2ac 100%);
    display: flex;
    align-items: center;
    justify-content: center;
  }
  .wordmark {
    font-family: "Marcellus", serif;
    font-size: 46px;
    color: var(--wordmark);
    letter-spacing: 1px;
    margin-top: 160px;
    white-space: nowrap;
  }
</style>
</head>
<body>
  <div class="card">
    <h1 class="holders">Paula &amp; Oskar Dunbeck</h1>
    <ul class="services">
      <li>PRIVATE OR GROUP YOGA</li>
      <li>RECONNECTIVE HEALING</li>
      <li>KITESURFING LESSONS</li>
      <li>MASSAGE</li>
    </ul>
    <p class="address">Calle del<br>Almendro 57 Villamar<br>de la Costa</p>
    <ul class="contact">
      <li>
        <svg viewBox="0 0 16 16" aria-hidden="true"><rect x="4" y="1" width="8" height="14" rx="1.5" fill="none" stroke="#4aa89c" stroke-width="1.6"/><circle cx="8" cy="12.3" r="0.9" fill="#4aa89c"/></svg>
        0046 731 402687
      </li>
      <li>
        <svg viewBox="0 0 16 16" aria-hidden="true"><rect x="1.5" y="4" width="13" height="9" fill="#4aa89c"/><path d="M1.5 4 L8 9 L14.5 4" fill="none" stroke="#1b2742" stroke-width="1.2"/></svg>
        info@brightmeadow.example
      </li>
      <li>
        <svg viewBox="0 0 16 16" aria-hidden="true"><circle cx="8" cy="8" r="6.5" fill="#4aa89c"/><path d="M1.5 8 H14.5 M8 1.5 C5 5 5 11 8 14.5 M8 1.5 C11 5 11 11 8 14.5" fill="none" stroke="#1b2742" stroke-width="1"/></svg>
        www.brightmeadow.example
      </li>
    </ul>
    <div class="emblem">
      <span class="wordmark">BRIGHTMEADOW</span>
    </div>
  </div>
</body>
</html>
```